New Slow Cooker Liners Packing design

--We have a total of four product variants:
1.two “Oven Bags” and two“Slow Cooker Liners”.
2.Each product variant requires both box packaging and paper card packaging.
3.Both the box packaging and paper card packaging should have a single size for each type.
4.Our brand is “Brava Nest”, But to these product we want to use "Brava Nest / Pantrova Select" as DBA on the packing.
which has its own logo and color scheme. You can use this color scheme for the design, but it’s not mandatory to use the exact same colors.
5.Alternatively, you can create a completely new color scheme, subtly incorporating the existing Brava Nest colors and design elements as text.
6.While maintaining a consistent style, ensure that there are distinctive differences between the packaging designs. For example, consider using different colors for certain elements.
7.The “how to use” section should include three photos, without any accompanying text.
8.The front design of the cardboard packaging should be similar to the front design of the box packaging.
9.The attached pdf is a design instruction, read it may help you.

```html
<!DOCTYPE html>
<html lang="en">
<head>
<meta charset="utf-8">
<title>Brava Nest Slow Cooker Liners – Box Front</title>
<link rel="stylesheet" href="https://fonts.googleapis.com/css2?family=Fredoka:wght@600;700&family=Montserrat:wght@600;700;800&display=swap">
<style>
  :root {
    --backdrop: #d9d9d9;
    --panel-dark: #232326;
    --panel-wave: #38373d;
    --lime: #cfdc1f;
    --green: #7dbb21;
    --green-bright: #a6d63a;
    --navy: #1b3347;
    --ink: #1c1c1c;
    --white: #ffffff;
    --steel: #9a9ea3;
    --stew: #5a3a22;
  }
  * { box-sizing: border-box; margin: 0; padding: 0; }
  html, body {
    width: 1200px; height: 830px; overflow: hidden;
    background: var(--backdrop);
  }
  .box-front {
    position: absolute; left: 50px; top: 160px;
    width: 1100px; height: 510px;
    background: var(--panel-dark);
    overflow: hidden;
    font-family: "Montserrat", sans-serif;
  }
  .wave { position: absolute; inset: 0; }
  .right-glow {
    position: absolute; right: 0; top: 0; width: 190px; height: 100%;
    background: linear-gradient(90deg, rgba(125,187,33,0) 0%, var(--green) 55%, var(--green-bright) 100%);
  }
  .brand {
    position: absolute; left: 222px; top: 12px;
    display: flex; align-items: center; gap: 10px;
    font-family: "Fredoka", sans-serif; font-weight: 700;
    font-size: 40px; line-height: 1; color: var(--lime);
  }
  .brand-dot {
    width: 18px; height: 18px; border-radius: 50%;
    background: var(--lime);
  }
  .title {
    position: absolute; left: 40px; top: 92px;
    font-family: "Fredoka", sans-serif; font-weight: 700;
    font-size: 110px; line-height: 1; color: var(--lime);
    letter-spacing: -1px; white-space: nowrap;
    -webkit-text-stroke: 14px var(--green);
    paint-order: stroke fill;
    transform: rotate(-1.5deg); transform-origin: left center;
  }
  .title-tag {
    position: absolute; left: 175px; top: 205px;
    width: 390px; height: 80px;
    background: var(--navy);
    border: 5px solid var(--green);
    border-radius: 14px 40px 14px 40px;
    transform: rotate(-1.5deg) skewX(-10deg);
  }
  .title-tag span {
    display: block; transform: skewX(10deg);
    text-align: center; line-height: 70px;
    font-family: "Montserrat", sans-serif; font-weight: 800; font-style: italic;
    font-size: 52px; letter-spacing: 16px; color: var(--white);
  }
  .tagline {
    position: absolute; left: 122px; top: 296px;
    font-weight: 700; font-size: 28px; line-height: 1; color: var(--white);
    white-space: nowrap;
    transform: rotate(-2deg); transform-origin: left center;
  }
  .count-band {
    position: absolute; left: 0; top: 340px;
    width: 720px; height: 118px;
  }
  .count-text {
    position: absolute; left: 106px; top: 382px;
    display: flex; align-items: center; gap: 16px;
    font-weight: 800; font-size: 40px; line-height: 1; color: var(--ink);
    white-space: nowrap;
    transform: rotate(-2deg); transform-origin: left center;
  }
  .count-text .divider {
    width: 0; height: 42px; border-left: 2px dotted var(--ink);
  }
  .size {
    position: absolute; left: 146px; top: 462px;
    font-weight: 600; font-size: 24px; line-height: 1; color: var(--white);
    white-space: nowrap;
    transform: rotate(-1.5deg); transform-origin: left center;
  }
  .product-photo {
    position: absolute; left: 672px; top: 74px;
    width: 428px; height: 392px;
    border-radius: 24px 0 0 24px;
    background: linear-gradient(180deg, var(--stew) 0%, #6e5a4a 40%, var(--steel) 100%);
  }
  .badge {
    position: absolute; left: 880px; top: 8px;
    width: 98px; height: 98px; border-radius: 50%;
    background: var(--white);
    display: flex; align-items: center; justify-content: center;
    text-align: center;
    font-weight: 800; font-size: 18px; line-height: 1.3; color: var(--ink);
  }
</style>
</head>
<body>
  <section class="box-front">
    <svg class="wave" viewBox="0 0 1100 510" preserveAspectRatio="none" aria-hidden="true">
      <path d="M0 0 H820 C700 40 560 90 420 85 C300 80 200 60 90 20 L0 0 Z" fill="var(--panel-wave)"/>
    </svg>
    <div class="right-glow"></div>

    <div class="brand"><span class="brand-dot"></span>Brava Nest</div>

    <h1 class="title">Slow Cooker</h1>
    <div class="title-tag"><span>LINERS</span></div>

    <p class="tagline">Keep Pot Clean. Seal in Flavours</p>

    <svg class="count-band" viewBox="0 0 720 118" preserveAspectRatio="none" aria-hidden="true">
      <polygon points="0,30 720,0 720,80 0,114 36,72" fill="var(--green)"/>
      <line x1="90" y1="32" x2="570" y2="14" stroke="var(--ink)" stroke-width="1.5" stroke-dasharray="2 3"/>
      <line x1="90" y1="104" x2="570" y2="86" stroke="var(--ink)" stroke-width="1.5" stroke-dasharray="2 3"/>
    </svg>
    <div class="count-text"><span>8 LINERS</span><span class="divider"></span><span>LARGE SIZE</span></div>

    <p class="size">12IN x 12IN (304mm X 304 mm)</p>

    <div class="product-photo" role="img" aria-label="Photo of a steel slow cooker lined with a clear liner, filled with steaming beef stew"></div>

    <div class="badge">BPA<br>FREE</div>
  </section>
</body>
</html>
```